Wealth Education Business Needs Sharp Business Card Design

We need a business card design for a recently launched investor education business called Harbor Crest.

The final design should promote security, empowerment, self improvement and financial gain. The card will ideally promote the stature of the business.

For more information and colours please visit harborcrest.com.au

Target Market(s)

Corporate executives and high net worth individuals

Industry/Entity Type

Education

Contact Information for Business Card

```html
<!DOCTYPE html>
<html lang="en">
<head>
<meta charset="utf-8">
<title>Harbor Crest Business Card</title>
<link href="https://fonts.googleapis.com/css2?family=Oswald:wght@400;500;600&family=Open+Sans:wght@400;600&display=swap" rel="stylesheet">
<style>
  :root {
    --navy: #1b2a3d;
    --teal: #1f8a8f;
    --teal-light: #3aa3a6;
    --ink: #2b2f36;
    --muted: #7d8794;
    --paper: #ffffff;
    --stage: #e9e7e3;
  }
  * { box-sizing: border-box; margin: 0; padding: 0; }
  html, body { width: 1200px; height: 902px; overflow: hidden; }
  body {
    background: var(--stage);
    font-family: "Open Sans", Arial, sans-serif;
    position: relative;
  }
  .card {
    position: absolute;
    left: 340px;
    width: 520px;
    height: 300px;
    border-radius: 14px;
    overflow: hidden;
    box-shadow: 0 6px 18px rgba(0,0,0,0.18);
  }

  /* Front */
  .card-front { top: 100px; background: var(--navy); color: var(--paper); text-align: center; }
  .front-brand {
    position: absolute; top: 92px; left: 0; right: 0;
    display: flex; justify-content: center; align-items: center; gap: 14px;
  }
  .brand-dot { width: 26px; height: 26px; border-radius: 50%; background: var(--teal-light); flex: none; }
  .front-name {
    font-family: "Oswald", Arial, sans-serif; font-weight: 600;
    font-size: 46px; letter-spacing: 2px; line-height: 1; color: var(--paper);
  }
  .front-tagline {
    position: absolute; top: 152px; left: 0; right: 0;
    font-family: "Oswald", Arial, sans-serif; font-weight: 400;
    font-size: 15px; letter-spacing: 7px; color: var(--teal-light);
  }
  .front-web {
    position: absolute; top: 232px; left: 0; right: 0;
    font-size: 12px; color: var(--muted); letter-spacing: 0.5px;
  }

  /* Back */
  .card-back { top: 480px; background: var(--paper); color: var(--ink); }
  .back-shapes { position: absolute; inset: 0; }
  .back-brand {
    position: absolute; left: 36px; top: 96px;
    display: flex; align-items: center; gap: 10px;
  }
  .back-brand .brand-dot { width: 20px; height: 20px; background: var(--teal); }
  .back-name {
    font-family: "Oswald", Arial, sans-serif; font-weight: 500;
    font-size: 26px; letter-spacing: 1px; color: var(--ink); line-height: 1;
    white-space: nowrap;
  }
  .back-address {
    position: absolute; left: 36px; top: 150px;
    font-size: 13px; line-height: 1.45; color: var(--ink);
  }
  .person {
    position: absolute; right: 24px; top: 24px; text-align: right;
  }
  .person-name {
    font-family: "Oswald", Arial, sans-serif; font-weight: 600;
    font-size: 17px; letter-spacing: 0.5px; color: var(--ink);
  }
  .person-name .accent { color: var(--teal); }
  .person-title { font-size: 12px; color: var(--ink); }
  .contacts {
    position: absolute; right: 24px; top: 104px; list-style: none; text-align: right;
  }
  .contacts li {
    font-size: 12px; line-height: 1.85; color: var(--ink); white-space: nowrap;
    display: flex; justify-content: flex-end; align-items: center; gap: 8px;
  }
  .contacts svg { width: 11px; height: 11px; fill: var(--ink); flex: none; }
  .web-band {
    position: absolute; right: 24px; bottom: 18px;
    font-size: 13px; color: var(--paper); white-space: nowrap;
    display: flex; align-items: center; gap: 8px;
  }
  .web-band svg { width: 13px; height: 13px; flex: none; }
</style>
</head>
<body>

<section class="card card-front">
  <div class="front-brand">
    <span class="brand-dot"></span>
    <span class="front-name">HARBOR CREST</span>
  </div>
  <p class="front-tagline">STUDY GROW THRIVE</p>
  <p class="front-web">www.harborcrest.com.au</p>
</section>

<section class="card card-back">
  <svg class="back-shapes" viewBox="0 0 520 300" preserveAspectRatio="none" aria-hidden="true">
    <path class="divider" d="M280 0 V48 L288 56 L280 64 V300" fill="none" stroke="var(--teal)" stroke-width="1.5"/>
    <path class="teal-band" d="M0 300 V290 L280 276 V300 Z" fill="var(--teal)"/>
    <path class="navy-band" d="M280 300 V264 C280 252 288 246 302 244 L520 232 V300 Z" fill="var(--navy)"/>
  </svg>

  <div class="back-brand">
    <span class="brand-dot"></span>
    <span class="back-name">HARBOR CREST</span>
  </div>
  <p class="back-address">Level 2, 48 Quayside Street<br>Portview VIC 3999</p>

  <div class="person">
    <p class="person-name"><span class="accent">YOUR</span> NAME</p>
    <p class="person-title">Title</p>
  </div>

  <ul class="contacts">
    <li>1300 555 014
      <svg viewBox="0 0 24 24"><path d="M6.6 10.8a15.1 15.1 0 006.6 6.6l2.2-2.2c.3-.3.7-.4 1-.2 1.1.4 2.3.6 3.6.6.6 0 1 .4 1 1V20c0 .6-.4 1-1 1A17 17 0 013 4c0-.6.4-1 1-1h3.5c.6 0 1 .4 1 1 0 1.3.2 2.5.6 3.6.1.3 0 .7-.2 1z"/></svg>
    </li>
    <li>+613 5550 2417
      <svg viewBox="0 0 24 24"><path d="M7 2h10a2 2 0 012 2v16a2 2 0 01-2 2H7a2 2 0 01-2-2V4a2 2 0 012-2zm0 3v12h10V5zm5 13.5a1 1 0 100 2 1 1 0 000-2z"/></svg>
    </li>
    <li>support@harborcrest.com.au
      <svg viewBox="0 0 24 24"><path d="M3 5h18v14H3zm2 2v.5l7 5 7-5V7zm0 3v7h14v-7l-7 5z"/></svg>
    </li>
  </ul>

  <p class="web-band">
    <svg viewBox="0 0 24 24" fill="none" stroke="#ffffff" stroke-width="2"><circle cx="12" cy="12" r="9"/><path d="M3 12h18M12 3c3 3 3 15 0 18M12 3c-3 3-3 15 0 18"/></svg>
    www.harborcrest.com.au
  </p>
</section>

</body>
</html>
```